Youth Lifting Youth Business Card. We have existing logo

We need a business card design from an existing logo.
Our logo is in black and white but would love to add in the color burgundy but we're open to any color. Our website is www.youthliftingyouthmv.org

Target Market(s)

corporations and foundations who will be donating

Industry/Entity Type

Business

Contact Information for Business Card

Address: 2318 Marwick Ave Santa Barbara, CA 93110
Name: Corin Halvorsen
Founder email: corin.halvorsen@youthliftingyouthmv.org
Phone: 805-637-9081

Requirements
Nice to have
• Our colors are burgundy and white, but that's not a necessity

```html
<!DOCTYPE html>
<html lang="en">
<head>
<meta charset="utf-8">
<title>Youth Lifting Youth Business Card</title>
<link href="https://fonts.googleapis.com/css2?family=Cinzel:wght@400;600&family=Arimo:wght@400&display=swap" rel="stylesheet">
<style>
  :root {
    --page: #e9e7e3;
    --card-black: #0b0b0b;
    --stripe-light: #bdbdbd;
    --stripe-mid: #7a7a7a;
    --panel: #ffffff;
    --ink: #111111;
    --rule: #555555;
  }
  * { margin: 0; padding: 0; box-sizing: border-box; }
  html, body { width: 1200px; height: 800px; overflow: hidden; background: var(--page); }
  .card {
    position: absolute; left: 75px; top: 100px;
    width: 1050px; height: 600px;
    background: var(--card-black);
    box-shadow: 0 18px 40px rgba(0,0,0,0.25);
    overflow: hidden;
  }
  .card-stripes { position: absolute; inset: 0; }
  .card-panel {
    position: absolute; left: 0; right: 0; top: 56px; height: 450px;
    background: var(--panel);
  }
  .identity { position: absolute; left: 70px; top: 40px; }
  .identity-name {
    font-family: "Cinzel", serif; font-weight: 600;
    font-size: 46px; letter-spacing: 1px; color: var(--ink); line-height: 1;
  }
  .identity-role {
    font-family: "Cinzel", serif; font-weight: 400;
    font-size: 22px; letter-spacing: 1.5px; color: var(--ink); margin-top: 4px;
  }
  .rule { position: absolute; height: 1px; background: var(--rule); }
  .rule-top { left: 40px; width: 700px; top: 140px; }
  .org { position: absolute; left: 70px; top: 215px; display: flex; align-items: center; gap: 18px; }
  .org-mark { width: 58px; height: 58px; border-radius: 50%; border: 2px solid var(--ink); flex: none; }
  .org-name {
    font-family: "Cinzel", serif; font-weight: 400; font-size: 22px;
    line-height: 1.25; color: var(--ink); width: 240px;
  }
  .contact { position: absolute; right: 60px; font-family: "Arimo", sans-serif; color: var(--ink); text-align: right; }
  .contact-address { top: 230px; font-size: 26px; line-height: 1.3; }
  .rule-address { right: 40px; width: 420px; top: 318px; }
  .contact-lines { top: 345px; font-size: 24px; line-height: 1; }
  .contact-line { display: flex; align-items: center; justify-content: flex-end; gap: 22px; margin-bottom: 18px; }
  .contact-icon { width: 30px; height: 30px; flex: none; }
  .rule-bottom { right: 40px; width: 430px; top: 455px; }
</style>
</head>
<body>
  <div class="card">
    <svg class="card-stripes" width="1050" height="600" viewBox="0 0 1050 600" aria-hidden="true">
      <polygon points="610,0 650,0 720,56 680,56" fill="var(--stripe-light)"/>
      <polygon points="650,0 670,0 740,56 720,56" fill="var(--stripe-mid)"/>
      <polygon points="200,506 240,506 150,600 110,600" fill="var(--stripe-light)"/>
      <polygon points="240,506 260,506 170,600 150,600" fill="var(--stripe-mid)"/>
      <polygon points="560,506 600,506 690,600 650,600" fill="var(--stripe-light)"/>
      <polygon points="600,506 620,506 710,600 690,600" fill="var(--stripe-mid)"/>
    </svg>
    <div class="card-panel">
      <div class="identity">
        <div class="identity-name">Corin Halvorsen</div>
        <div class="identity-role">Founder</div>
      </div>
      <div class="rule rule-top"></div>
      <div class="org">
        <div class="org-mark"></div>
        <div class="org-name">Mar Vista Youth Lifting Youth Foundation</div>
      </div>
      <div class="contact contact-address">2318 Marwick Ave Santa Barbara,<br>CA 93110</div>
      <div class="rule rule-address"></div>
      <div class="contact contact-lines">
        <div class="contact-line">
          <span>805-637-9081</span>
          <svg class="contact-icon" viewBox="0 0 30 30" aria-hidden="true">
            <circle cx="15" cy="15" r="13" fill="none" stroke="var(--ink)" stroke-width="2"/>
            <path d="M10 8 l3 0 l1 4 l-2 1.5 q1.5 3 4.5 4.5 l1.5 -2 l4 1 l0 3 q-1 1.5 -3 1.5 q-10 -1 -11 -11 q0 -2 2 -2.5z" fill="var(--ink)"/>
          </svg>
        </div>
        <div class="contact-line">
          <span>corin.halvorsen@youthliftingyouthmv.org</span>
          <svg class="contact-icon" viewBox="0 0 30 30" aria-hidden="true">
            <circle cx="15" cy="15" r="13" fill="none" stroke="var(--ink)" stroke-width="2"/>
            <rect x="8" y="10" width="14" height="10" fill="var(--ink)"/>
            <path d="M8 10 l7 6 l7 -6" fill="none" stroke="var(--panel)" stroke-width="1.5"/>
          </svg>
        </div>
      </div>
      <div class="rule rule-bottom"></div>
    </div>
  </div>
</body>
</html>
```